Financial Advisor Resource Firm needs business card design

Need business card design for company in Omaha NE called Meridale Circle. We provide resources to financial advisors....workshop programs, retirement analysis, and insurance planning. I would like to see designs that use grays, greens, black, and white colors. The final design should communicate 'collaboration' and be simple yet attractive to financial planning clients. I will attached our logo and another picture of a puzzle piece coming together. I would like the incorporate the puzzle picture somehow, maybe on the back somehow, with color or just the gray scale....OR, the picture be the front of the card with 'Meridale' definition on it (see upload) and then company logo, employee name, title, address on the back (see ppt uploaded). The following disclosure needs to be included somewhere- Advisory services offered through Stonebrook Assets, LLC.
Updates

I uploaded a svg and ai file of the logo

Target Market(s)

Financial planning clients and financial advisors....so pretty diverse age range of about 40-70.

Industry/Entity Type

Financial Planning

Contact Information for Business Card

Tobias L. Fenwright, MBA
Founder/President
5287 E. Larkin Road
Suite 230
Omaha, NE 68190
Phone- (402) 555-0147
Cell- (402) 555-0183
Fax- (402) 555-0129
email- tobias@meridaleplan.example
web address- www.meridaleplan.example

Colors
1b1b1b
474747
d3d3d3
ffffff
9bcb3c
abd036

Requirements
Must have
• Must include logo provided, must be 2 sided, and must have disclosure...all of these items listed in project description

```html
<!DOCTYPE html>
<html lang="en">
<head>
<meta charset="utf-8">
<title>Meridale Circle — Business Card</title>
<link rel="stylesheet" href="https://fonts.googleapis.com/css2?family=Montserrat:wght@400;500;600&display=swap">
<style>
  :root {
    --ink: #1b1b1b;
    --slate: #474747;
    --mist: #d3d3d3;
    --paper: #ffffff;
    --leaf: #9bcb3c;
    --lime: #abd036;
    --stage: #f6f6f6;
  }
  * { box-sizing: border-box; margin: 0; padding: 0; }
  html, body { width: 1200px; height: 900px; overflow: hidden; }
  body {
    background: var(--stage);
    font-family: "Montserrat", sans-serif;
    position: relative;
  }
  .card {
    position: absolute;
    left: 294px;
    width: 612px;
    height: 350px;
    box-shadow: 0 8px 22px rgba(0,0,0,0.28);
    overflow: hidden;
  }
  .card-front { top: 71px; background: var(--ink); }
  .card-back { top: 478px; background: var(--paper); }

  .front-brand {
    position: absolute;
    left: 0; right: 0; top: 140px;
    text-align: center;
  }
  .front-brand .brand-name {
    font-size: 38px;
    font-weight: 500;
    letter-spacing: 1px;
    color: var(--paper);
    text-transform: uppercase;
  }
  .tagline {
    position: absolute;
    left: 0; right: 0; top: 287px;
    text-align: center;
    color: var(--paper);
    font-size: 14.5px;
    line-height: 20px;
  }
  .accent { color: var(--leaf); font-weight: 500; }

  .back-photo {
    position: absolute;
    right: 0; top: 0;
    width: 360px; height: 350px;
    background:
      linear-gradient(90deg, var(--paper) 0%, rgba(255,255,255,0.6) 25%, rgba(255,255,255,0) 55%),
      linear-gradient(0deg, var(--paper) 0%, rgba(255,255,255,0) 30%),
      radial-gradient(ellipse at 60% 50%, #5d636b 0%, #8d939a 40%, #c4c8cc 75%, #eef0f2 100%);
  }
  .back-content {
    position: absolute;
    left: 40px; top: 0;
    width: 320px;
    height: 350px;
  }
  .back-brand {
    position: absolute;
    top: 52px;
    font-size: 26px;
    font-weight: 500;
    letter-spacing: 0.5px;
    color: var(--ink);
    text-transform: uppercase;
    white-space: nowrap;
  }
  .person {
    position: absolute;
    top: 112px;
    white-space: nowrap;
  }
  .person-name {
    font-size: 19px;
    font-weight: 500;
    color: var(--slate);
    text-transform: uppercase;
    letter-spacing: 0.3px;
  }
  .person-name .surname { color: var(--leaf); }
  .person-name .credential { font-size: 13px; text-transform: none; }
  .person-title { font-size: 13.5px; color: var(--slate); margin-top: 2px; }
  .address {
    position: absolute;
    top: 163px;
    font-size: 15px;
    line-height: 19px;
    color: var(--leaf);
    white-space: nowrap;
  }
  .contacts {
    position: absolute;
    top: 213px;
    list-style: none;
  }
  .contacts li {
    display: flex;
    align-items: center;
    height: 24.5px;
    font-size: 15px;
    color: var(--slate);
    white-space: nowrap;
  }
  .contacts svg { width: 18px; height: 18px; margin-right: 11px; fill: var(--leaf); }
  .disclosure {
    position: absolute;
    top: 324px;
    font-size: 9px;
    line-height: 12px;
    color: var(--slate);
    white-space: nowrap;
  }
</style>
</head>
<body>
  <section class="card card-front" aria-label="Card front">
    <div class="front-brand">
      <span class="brand-name">Meridale Circle</span>
    </div>
    <p class="tagline">
      To come <span class="accent">TOGETHER</span> and <span class="accent">UNITE</span> in common interest and <span class="accent">FOCUS</span><br>
      www.<span class="accent">meridaleplan</span>.example
    </p>
  </section>

  <section class="card card-back" aria-label="Card back">
    <div class="back-photo" role="img" aria-label="Grayscale photo of hands joining puzzle pieces together"></div>
    <div class="back-content">
      <div class="back-brand">Meridale Circle</div>
      <div class="person">
        <div class="person-name">Tobias L. <span class="surname">Fenwright</span><span class="credential">, MBA</span></div>
        <div class="person-title">Founder | President</div>
      </div>
      <div class="address">5287 E. Larkin Road<br>Suite 230, Omaha, NE 68190</div>
      <ul class="contacts">
        <li>
          <svg viewBox="0 0 24 24" aria-hidden="true"><path d="M6.6 10.8a15.1 15.1 0 0 0 6.6 6.6l2.2-2.2c.3-.3.7-.4 1-.2 1.1.4 2.3.6 3.6.6.6 0 1 .4 1 1V20c0 .6-.4 1-1 1A17 17 0 0 1 3 4c0-.6.4-1 1-1h3.5c.6 0 1 .4 1 1 0 1.3.2 2.5.6 3.6.1.3 0 .7-.2 1z"/></svg>
          (402) 555 - 0147
        </li>
        <li>
          <svg viewBox="0 0 24 24" aria-hidden="true"><path d="M7 1h10a2 2 0 0 1 2 2v18a2 2 0 0 1-2 2H7a2 2 0 0 1-2-2V3a2 2 0 0 1 2-2zm0 3v14h10V4zm5 15.5a1.2 1.2 0 1 0 0 2.4 1.2 1.2 0 0 0 0-2.4z"/></svg>
          (402) 555 - 0183
        </li>
        <li>
          <svg viewBox="0 0 24 24" aria-hidden="true"><path d="M3 7h4v15H3zM8 9h13v13H8zm2 2v3h9v-3zm0 5v2h2v-2zm4 0v2h2v-2zm4 0v2h1v-2zM10 2h9v6h-9z"/></svg>
          (402) 555 - 0129
        </li>
        <li>
          <svg viewBox="0 0 24 24" aria-hidden="true"><path d="M2 5h20v2l-10 6L2 7zm0 4.3 10 6 10-6V19H2z"/></svg>
          tobias@meridaleplan.example
        </li>
      </ul>
      <p class="disclosure">Advisory services offered through Stonebrook Assets, LLC.</p>
    </div>
  </section>
</body>
</html>
```